Harrow grounds and gardens

Lawn Maintenance, Spring Fall Clean Ups, Stone Walls & Walkways, Commercial and Residental Snow Removal carpentry and handyman services

Industry/Entity Type

Carpentry

Contact Information for Business Card

Harrow Grounds and Gardens 83 Pebble Marsh Rd Fernbrook NY 10950 555 261 3087 Cell 555319 5402

```html
<!DOCTYPE html>
<html lang="en">
<head>
<meta charset="utf-8">
<title>Harrow Grounds and Gardens – Business Card</title>
<link rel="stylesheet" href="https://fonts.googleapis.com/css2?family=Ubuntu:wght@300;400;500;700&display=swap">
<style>
  :root {
    --bg: #e9e9e7;
    --card-edge: #f2f2f2;
    --green: #139a48;
    --grey-text: #8a8a8a;
    --grey-dark: #6f6f6f;
  }
  * { box-sizing: border-box; margin: 0; padding: 0; }
  html, body {
    width: 1200px; height: 818px; overflow: hidden;
    background: var(--bg);
    font-family: "Ubuntu", sans-serif;
  }
  .stage {
    width: 1200px; height: 818px;
    display: flex; align-items: center; justify-content: center;
  }
  .card {
    position: relative;
    width: 900px; height: 514px;
    border-radius: 22px;
    background: linear-gradient(160deg, #ffffff 0%, #fbfbfb 55%, #efefef 100%);
    box-shadow: 0 3px 0 var(--card-edge), 0 6px 0 #e3e3e3, 0 18px 40px rgba(0,0,0,0.18);
  }
  .brand {
    position: absolute; left: 58px; top: 72px;
    display: flex; align-items: center; gap: 22px;
  }
  .brand-mark {
    width: 128px; height: 128px; border-radius: 50%;
    background: radial-gradient(circle at 45% 40%, #9fc7a3 0%, #5b9a4e 55%, #2f7a2f 100%);
    border: 5px solid var(--green);
    flex: none;
  }
  .brand-name {
    color: var(--green);
    font-weight: 700;
    line-height: 1;
  }
  .brand-name .word { display: block; font-size: 88px; letter-spacing: -1px; }
  .brand-name .rest { display: block; font-size: 34px; margin-top: 4px; letter-spacing: 0.5px; }
  .employee {
    position: absolute; right: 60px; top: 212px;
    color: var(--green); font-weight: 700; font-size: 38px;
  }
  .divider {
    position: absolute; left: 230px; right: 48px; top: 268px;
    height: 2px; background: var(--green);
  }
  .contact {
    position: absolute; left: 60px; top: 300px;
    color: var(--grey-text); font-size: 30px; line-height: 1.28;
    font-style: normal; font-weight: 300;
  }
  .contact .phone { display: flex; align-items: center; gap: 12px; }
  .contact svg { width: 26px; height: 26px; flex: none; }
  .services {
    position: absolute; right: 52px; top: 300px;
    list-style: none; text-align: right;
    color: var(--grey-dark); font-size: 23px; line-height: 1.42; font-weight: 300;
  }
  .services li::after {
    content: ""; display: inline-block;
    width: 8px; height: 8px; border-radius: 50%;
    background: var(--green); margin-left: 16px; vertical-align: middle;
  }
  .services li.cont::after { visibility: hidden; }
</style>
</head>
<body>
<main class="stage">
  <article class="card">
    <header class="brand">
      <div class="brand-mark" role="img" aria-label="Photo of a house with garden and lawn inside a circle"></div>
      <h1 class="brand-name"><span class="word">Harrow</span><span class="rest">Grounds and Gardens</span></h1>
    </header>

    <p class="employee">Employee Name</p>
    <div class="divider"></div>

    <address class="contact">
      <div>83 Pebble Marsh Rd</div>
      <div>Fernbrook NY 10950</div>
      <div class="phone">
        <svg viewBox="0 0 26 26" aria-hidden="true"><rect width="26" height="26" rx="3" fill="var(--green)"/><rect x="9" y="5" width="8" height="16" rx="1.5" fill="#fff"/><rect x="10.5" y="7" width="5" height="8" fill="var(--green)"/></svg>
        <span>555319 5402</span>
      </div>
      <div class="phone">
        <svg viewBox="0 0 26 26" aria-hidden="true"><rect width="26" height="26" rx="3" fill="var(--green)"/><path d="M6 10h14v10H6z" fill="#fff"/><rect x="9" y="6" width="8" height="5" rx="1" fill="#fff"/><circle cx="13" cy="15" r="2.5" fill="var(--green)"/></svg>
        <span>555 261 3087</span>
      </div>
    </address>

    <ul class="services">
      <li>Lawn Maintenance</li>
      <li>Spring Fall Clean Ups</li>
      <li>Stone Walls &amp; Walkways</li>
      <li>Commercial and Residental</li>
      <li>Snow Removal carpentry and</li>
      <li class="cont">handyman services</li>
    </ul>
  </article>
</main>
</body>
</html>
```